Business card

We need a business card design for our company based in Auckland , New Zealand called 'Ridge + Studio Ltd'. We provide architectural services. We would like to see designs that use the max. three colours (such as white, black, grey) The final design should communicate financial safety and growth."
Also I will provide our company logo. I would like to the logo to be embeded onto our business card.

Target Market(s)

new residential house, alteration & addition & light commericila design & drafting service

Industry/Entity Type

Architecture

Contact Information for Business Card

Company name: ridge + studio Ltd.
Name: Mark Delford
Job title: architectural designer & Design LBP
email address: mark@rplusd.co.nz
mobile number: 02 5163 2290
web site: www.rplusd.co.nz

Requirements
Must have
• My project must have..
• - embeded logo (attached company logo)
• I don't have a bigger version for our company logo, but I have one old one, so you can remove the word from it)
• - insert the attached small BKTW logo & LBP logo
• - creative, simple and clear business card.
• - Max. three colours
Nice to have
• - Here are the samples I would like to share with you: http://www.plimvora.com/blog/minimalistic-business-card-designs/
• I would like to have my business card like one of the creation.
Should not have
• TBA

```html
<!DOCTYPE html>
<html lang="en">
<head>
<meta charset="utf-8">
<title>Ridge + Studio Ltd — Business Card</title>
<link href="https://fonts.googleapis.com/css2?family=Open+Sans:wght@400;600;700&display=swap" rel="stylesheet">
<style>
  :root {
    --page: #e7e5e3;
    --card: #f4f4f3;
    --card-edge: #c9c8c6;
    --ink: #1b1b1b;
    --band-dark: #1e1e1e;
    --band-grey: #4a4a4a;
    --band-text: #e9e9e9;
    --muted: #5c5c5c;
  }
  * { box-sizing: border-box; margin: 0; padding: 0; }
  html, body {
    width: 1200px; height: 969px; overflow: hidden;
    background: var(--page);
    font-family: "Open Sans", sans-serif;
  }
  .card {
    position: absolute; left: 180px; top: 250px;
    width: 840px; height: 470px;
    background: var(--card);
    border: 1px solid var(--card-edge);
    box-shadow: 0 10px 30px rgba(0,0,0,0.12);
  }
  .logo-row {
    position: absolute; left: 0; top: 70px; width: 100%; height: 150px;
  }
  .company-mark {
    position: absolute; left: 90px; top: 30px;
    display: flex; align-items: center; gap: 14px;
  }
  .company-mark .dot {
    width: 84px; height: 84px; border-radius: 50%;
    border: 8px solid var(--ink);
  }
  .company-mark .name {
    font-size: 22px; font-weight: 700; color: var(--ink); line-height: 1.15;
  }
  .association-mark {
    position: absolute; left: 400px; top: 48px;
    font-size: 50px; font-weight: 700; color: var(--ink); letter-spacing: -1px;
  }
  .divider {
    position: absolute; left: 590px; top: 20px;
    width: 1px; height: 110px; background: var(--ink);
  }
  .practitioner-badge {
    position: absolute; left: 612px; top: 22px;
    width: 106px; height: 106px; border-radius: 50%;
    background: var(--ink);
  }
  .title-band {
    position: absolute; left: 0; top: 270px; width: 840px; height: 62px;
    display: flex;
  }
  .title-band .person {
    width: 290px; background: var(--band-dark); color: var(--band-text);
    font-size: 27px; font-weight: 400; text-align: right;
    padding-right: 22px; line-height: 62px;
  }
  .title-band .role {
    flex: 1; background: var(--band-grey); color: var(--band-text);
    border-left: 3px solid var(--card);
    font-size: 24px; font-weight: 600; line-height: 62px; padding-left: 18px;
  }
  .contact {
    position: absolute; left: 0; top: 370px; width: 100%;
    text-align: center; color: var(--muted);
    font-size: 20px; line-height: 34px;
  }
</style>
</head>
<body>
  <section class="card">
    <div class="logo-row">
      <div class="company-mark">
        <span class="dot"></span>
        <span class="name">Ridge +<br>Studio</span>
      </div>
      <div class="association-mark">BKTW</div>
      <div class="divider"></div>
      <div class="practitioner-badge" role="img" aria-label="Licensed practitioner badge"></div>
    </div>
    <div class="title-band">
      <div class="person">Mark Delford</div>
      <div class="role">architectural designer &amp; Design LBP</div>
    </div>
    <div class="contact">
      <p>ridge + studio Ltd. | M : 02 5163 2290</p>
      <p>E : mark@rplusd.co.nz W : www.rplusd.co.nz</p>
    </div>
  </section>
</body>
</html>
```